Need a landing page design updated

Need an existing landing page perfected, want it too look similar to one of Quorbel's landing pages in that it flows and is really aesthetically pleasing. The link to the landing page is below. I need this design updated asap. Please take the content directly from the page.

http://verdantmoxfl.com/residential-services/

Target Market(s)

High end residential landscape customers on the gulf coast of Florida (Clearwater area)

Industry/Entity Type

Landscape Gardening

Font styles to use
Sans Serif
Decorative

Requirements
Must have
• I want to keep the written content the same on on the landing page, but would like to work on making both aesthetically appealing to the consumer. This is for high end residential clients on the gulf coast of florida, so think palm trees and sunny beaches with beautiful houses and gorgeous landscapes....look through www.verdantmoxfl.com home page for an example of the houses we landscape.
Nice to have
• Would like it to flow as you scroll similar to Quorbel's landing pages.
• Look at how Quorbel's landing page flows, want similar here.....
• https://www.quorbel.com/zentaphone-v/
Should not have
• this landing page must be beautiful and must make a lot of sense as you scroll, am looking for a work of art....please do not submit generic templates or anything that can be easily done....I need real artistry.

```html
<!DOCTYPE html>
<html lang="en">
<head>
<meta charset="utf-8">
<title>Verdantmox – Residential Landscaping</title>
<link href="https://fonts.googleapis.com/css2?family=Poppins:wght@300;400;500;600;700&display=swap" rel="stylesheet">
<style>
:root{
  --teal:#1a9fc7;
  --teal-dark:#1487ab;
  --grass:#3f7a23;
  --grass-dark:#23521a;
  --lime:#7bb42c;
  --sky:#3a9fd8;
  --ink:#2b2b2b;
  --body:#4a4a4a;
  --slate:#8e99a4;
  --slate-light:#a6b0bb;
  --paper:#f3f3f3;
  --white:#ffffff;
}
*{margin:0;padding:0;box-sizing:border-box}
html,body{width:1200px;height:3947px;overflow:hidden}
body{font-family:"Poppins",Arial,sans-serif;color:var(--body);background:var(--white);position:relative}
.block{position:absolute;left:0;width:1200px}

/* header */
.site-header{top:0;height:87px;background:var(--white)}
.brand{position:absolute;left:100px;top:28px;font-size:30px;font-weight:600;letter-spacing:1px;color:var(--teal);display:flex;align-items:center;gap:10px}
.brand-dot{width:14px;height:14px;border-radius:50%;background:var(--lime)}
.contact{position:absolute;right:100px;top:32px;text-align:right;font-size:12px;line-height:18px;color:var(--ink)}
.contact .call{color:var(--teal)}
.main-nav{top:87px;height:37px;background:var(--teal);display:flex;align-items:center;padding-left:106px;gap:26px}
.main-nav a{color:var(--white);font-size:12px;font-weight:600;text-decoration:none}

/* hero */
.hero{top:124px;height:397px;background:linear-gradient(90deg,var(--grass-dark),var(--grass) 60%,#2f6a1c)}
.hero-tools{position:absolute;right:0;top:0;width:640px;height:397px;background:linear-gradient(135deg,#6e7a72,#4a5a4d 55%,#2e6c2a);clip-path:polygon(30% 0,100% 0,100% 100%,0 100%)}
.hero-copy{position:absolute;left:97px;top:105px;width:580px;color:var(--white)}
.hero-copy h1{font-size:48px;font-weight:700;margin-bottom:14px}
.hero-copy p{font-size:20px;line-height:31px}

/* intro */
.intro{top:521px;height:316px;text-align:center}
.intro .lead{position:absolute;top:60px;width:100%;font-size:17px;line-height:28px;color:var(--ink)}
.intro .sub{position:absolute;top:202px;width:100%;font-size:14px;line-height:24px}

/* comparison */
.compare{top:837px;height:479px}
.compare .side{position:absolute;top:0;height:479px}
.side.generic{left:0;width:620px;background:linear-gradient(160deg,#8dc23a,var(--lime) 50%,#5a9a24)}
.side.tailored{left:590px;width:610px;background:linear-gradient(160deg,#4aaee2,var(--sky) 50%,#2f86c0);clip-path:polygon(0 0,100% 0,100% 100%,0 100%,30px 50%)}
.side h2{position:absolute;top:86px;font-size:29px;line-height:37px;font-weight:600;color:var(--white);text-transform:uppercase}
.side ul{position:absolute;top:184px;list-style:none;width:420px}
.side li{position:relative;padding-left:26px;font-size:13px;line-height:18px;color:var(--white);margin-bottom:16px}
.side li svg{position:absolute;left:0;top:2px}
.generic h2,.generic ul{left:97px}
.tailored h2,.tailored ul{left:60px}

/* benefits */
.benefits{top:1316px;height:525px;text-align:center}
.benefits h2{position:absolute;top:92px;width:100%;font-size:28px;line-height:38px;font-weight:500;color:var(--ink);text-transform:uppercase}
.benefit{position:absolute;top:218px;width:300px}
.benefit .icon{width:114px;height:114px;border-radius:50%;background:var(--teal);margin:0 auto 30px;display:flex;align-items:center;justify-content:center}
.benefit p{font-size:14px;line-height:22px}

/* feature rows */
.feature{overflow:visible}
.feature.eco{top:1841px;height:435px;background:var(--slate)}
.feature.schedule{top:2276px;height:402px;background:var(--slate-light)}
.photo-frame{position:absolute;border:3px solid var(--white);outline:1px solid rgba(255,255,255,.6);outline-offset:-12px}
.eco .photo-frame{left:100px;top:32px;width:402px;height:396px;background:linear-gradient(180deg,#7aa33a,#b58a3c 50%,#3f6a22)}
.schedule .photo-frame{left:697px;top:-58px;width:402px;height:434px;background:linear-gradient(150deg,#4f7a2a,#8b6a3e 45%,#5a8a30);z-index:2}
.feature-copy{position:absolute;color:var(--white)}
.eco .feature-copy{left:605px;top:128px;width:520px}
.schedule .feature-copy{left:97px;top:130px;width:540px}
.feature-copy h3{font-size:21px;line-height:30px;font-weight:600;text-transform:uppercase;margin-bottom:18px}
.feature-copy p{font-size:13px;line-height:21px}

/* testimonials */
.testimonials{top:2678px;height:422px;text-align:center}
.testimonials .lead{position:absolute;top:120px;width:100%;font-size:17px;line-height:28px;color:var(--ink)}
.testimonials blockquote{position:absolute;width:100%;font-size:14px;line-height:22px}
.q1{top:215px}.q2{top:290px}

/* flaws */
.flaws{top:3100px;height:394px;background:linear-gradient(90deg,var(--grass-dark),var(--grass) 60%,#2f6a1c)}
.flaws-shears{position:absolute;right:0;top:0;width:520px;height:394px;background:linear-gradient(200deg,#c89a8a,#3f6e24 45%,#2c5a1a)}
.flaws-copy{position:absolute;left:97px;top:120px;width:720px;color:var(--white)}
.flaws-copy h2{font-size:33px;line-height:43px;font-weight:700;margin-bottom:20px}
.flaws-copy p{font-size:20px;line-height:31px}

/* cta */
.cta{top:3494px;height:368px;background:var(--paper);text-align:center;color:var(--ink)}
.cta .q{position:absolute;top:64px;width:100%;font-size:15px}
.cta .r{position:absolute;top:104px;width:100%;font-size:15px}
.cta h2{position:absolute;top:136px;width:100%;font-size:20px;font-weight:400}
.cta .field{position:absolute;left:355px;width:487px;height:32px;border:1px solid #ccc;background:var(--white);text-align:left;padding:0 12px;font-size:11px;line-height:30px;color:#999}
.f1{top:192px}.f2{top:233px}
.cta .btn{position:absolute;left:536px;top:279px;width:128px;height:34px;background:var(--teal);color:var(--white);font-size:12px;line-height:34px}

/* footer */
.site-footer{top:3862px;height:85px;background:var(--teal);color:var(--white);text-align:center;font-size:15px;line-height:85px}
</style>
</head>
<body>

<header class="block site-header">
  <div class="brand"><span class="brand-dot"></span>VERDANTMOX</div>
  <div class="contact"><span class="call">Call Us Now On : 727-555-0148</span><br>Client Portal | Get A Free Quote</div>
</header>
<nav class="block main-nav">
  <a href="#">HOME</a><a href="#">ABOUT US</a><a href="#">RESIDENTIAL</a><a href="#">COMMERCIAL</a><a href="#">BLOG</a><a href="#">CONTACT US</a>
</nav>

<section class="block hero">
  <div class="hero-tools" role="img" aria-label="Garden tools, hose and gloves laid on a wooden deck beside the lawn"></div>
  <div class="hero-copy">
    <h1>Let’s guess:</h1>
    <p>You don’t have an abundance of free time. And, you simply don’t want to spend the little time you have – mowing a lawn and pruning the plants.</p>
  </div>
</section>

<section class="block intro">
  <p class="lead">You would probably like to spend that time the way you should, instead.<br>Enjoying the sunset in the privacy of your garden, watching a favorite TV show while lying<br>on a hammock, or throwing an occasional BBQ party with your friends and loved ones. Right?</p>
  <p class="sub">Getting an outdoor area of your dreams is not that difficult, nor expensive.<br>You can make this happen by getting a help from a landscaping company that offers tailor-made services.</p>
</section>

<section class="block compare">
  <div class="side generic" role="img" aria-label="House with a green front lawn">
    <h2>Generic landscaping<br>services:</h2>
    <ul>
      <li><svg width="16" height="14" viewBox="0 0 16 14"><path d="M1 7l5 5L15 2" fill="none" stroke="#fff" stroke-width="2.5"/></svg>You pay for the bundle of services, regardless of whether you actually need them</li>
      <li><svg width="16" height="14" viewBox="0 0 16 14"><path d="M1 7l5 5L15 2" fill="none" stroke="#fff" stroke-width="2.5"/></svg>You get a generic service, not adjusted to the specific needs of your outdoor area</li>
      <li><svg width="16" height="14" viewBox="0 0 16 14"><path d="M1 7l5 5L15 2" fill="none" stroke="#fff" stroke-width="2.5"/></svg>the field team thinks of your property as just another task they have to complete</li>
    </ul>
  </div>
  <div class="side tailored" role="img" aria-label="Landscaped garden with a curved path">
    <h2>Tailor-made landscaping<br>services:</h2>
    <ul>
      <li><svg width="16" height="14" viewBox="0 0 16 14"><path d="M1 7l5 5L15 2" fill="none" stroke="#fff" stroke-width="2.5"/></svg>You pay only for the services your yard really needs.</li>
      <li><svg width="16" height="14" viewBox="0 0 16 14"><path d="M1 7l5 5L15 2" fill="none" stroke="#fff" stroke-width="2.5"/></svg>You get your garden’s specific issues solved, and specific requirements met</li>
      <li><svg width="16" height="14" viewBox="0 0 16 14"><path d="M1 7l5 5L15 2" fill="none" stroke="#fff" stroke-width="2.5"/></svg>The field team members take their time working on your property</li>
      <li><svg width="16" height="14" viewBox="0 0 16 14"><path d="M1 7l5 5L15 2" fill="none" stroke="#fff" stroke-width="2.5"/></svg>They get to learn all about your vision –<br>and make it a reality</li>
    </ul>
  </div>
</section>

<section class="block benefits">
  <h2>More benefits of having a<br>well-maintained yard:</h2>
  <div class="benefit" style="left:97px">
    <div class="icon"><svg width="58" height="50" viewBox="0 0 58 50"><rect x="2" y="2" width="54" height="46" fill="#fff"/><path d="M10 38l14-14 8 8 16-16" fill="none" stroke="#1a9fc7" stroke-width="4"/><path d="M40 14h9v9" fill="none" stroke="#1a9fc7" stroke-width="4"/></svg></div>
    <p>In some cases, a great-looking<br>lawn can increase your property’s<br>value up to 20%.</p>
  </div>
  <div class="benefit" style="left:450px">
    <div class="icon"><svg width="58" height="54" viewBox="0 0 58 54"><path d="M29 3L3 26h8v25h36V26h8z" fill="#fff"/><circle cx="29" cy="34" r="11" fill="#1a9fc7"/><text x="29" y="40" text-anchor="middle" font-family="Poppins,Arial,sans-serif" font-size="15" font-weight="700" fill="#fff">$</text></svg></div>
    <p>Your lawn and plants reduce the energy<br>consumption – countering the warming<br>effects of paved surfaces.</p>
  </div>
  <div class="benefit" style="left:803px">
    <div class="icon"><svg width="60" height="52" viewBox="0 0 60 52"><rect x="4" y="4" width="34" height="44" fill="none" stroke="#fff" stroke-width="3"/><path d="M12 4v44M20 4v44M28 4v44" stroke="#fff" stroke-width="3"/><path d="M40 26h14M48 19l7 7-7 7" fill="none" stroke="#fff" stroke-width="3"/></svg></div>
    <p>They act as giant dust filters, increasing<br>air quality, and removing carbon dioxide<br>from the atmosphere.</p>
  </div>
</section>

<section class="block feature eco">
  <div class="photo-frame" role="img" aria-label="Gardener in overalls carrying a watering can across a lawn"></div>
  <div class="feature-copy">
    <h3>Why should you care that Verdantmox employs the leading industry experts and uses modern, eco-friendly technical solutions?</h3>
    <p>That is why we’re able to transform your lawn into a green carpet and get your plants in a perfect health. All while keeping your vision and your budget on our minds.That is why our services actually enable you to reduce the operating expenses.</p>
  </div>
</section>

<section class="block feature schedule">
  <div class="feature-copy">
    <h3>Do you worry our services are going to disturb you while trying to unwind in the privacy of your own garden?</h3>
    <p>Our Client Service Operators Build A Schedule Around Your Needs -<br>Designed Not To Disturb You At All.</p>
  </div>
  <div class="photo-frame" role="img" aria-label="Top view of a person in a sun hat tending flowers beside a garden hose"></div>
</section>

<section class="block testimonials">
  <p class="lead">At Verdantmox, we do more than just keeping your landscape in a pristine state.<br>This is what some of our long-term clients say about our approach:</p>
  <blockquote class="q1">“We are delighted with your landscaping, both with the design and implementation.It’s not very<br>often these days that work exceeds expectations.”</blockquote>
  <blockquote class="q2">“Verdantmox are efficient, on-time, responsive, provide fair pricing, do outstanding work, have<br>great people, and actually follow up on their work.”</blockquote>
</section>

<section class="block flaws">
  <div class="flaws-shears" role="img" aria-label="Gloved hands trimming grass with hedge shears"></div>
  <div class="flaws-copy">
    <h2>Do our services have flaws?<br>Yes. They have two giant ones.</h2>
    <p>1. Your “new” garden will get all of your neighbors jealous.<br>2. Your friends will probably start inviting themselves over<br>more frequently.</p>
  </div>
</section>

<section class="block cta">
  <p class="q">So, what’s the next step to enriching your living area?</p>
  <p class="r">And getting you a garden from your dreams.</p>
  <h2>It’s simple, just book a no-obligations consultation</h2>
  <div class="field f1">Name</div>
  <div class="field f2">Phone OR Email</div>
  <div class="btn">Get Started</div>
</section>

<footer class="block site-footer">Copyright 2017 Verdantmox All Rights Reserved</footer>

</body>
</html>
```